Falkrin homes and renovations business card design.

Would like some new card designs utilizing my new logo that look professional. I am open to different colors on the logo or utilize the same ones we have. I like the original concept but would like to see some fresh ideas and build on what we have already done.

Target Market(s)

Custom home building industry, Real estate sales, Renovation projects.

Industry/Entity Type

Home Builder

Contact Information for Business Card

Falkrin Homes and Renovations
2871 96th Avenue
Velden, Alberta
T2R3W8
Home : 403- 718-4063 Cell: 403- 294-5170

My info is : Dax Falkrin, President and CEO
email: falkrinhomes@maildrop-example.net
Website: falkrinhomes-example.com
websit

Requirements
Must have
• Must Use my new logo design. I am open to different colors on the logo or utilize the same ones in the existing design. I can upload the original logo design if needed.

```html
<!DOCTYPE html>
<html lang="en">
<head>
<meta charset="utf-8">
<title>Falkrin Homes and Renovations – Business Card</title>
<link href="https://fonts.googleapis.com/css2?family=Montserrat:wght@400;600&display=swap" rel="stylesheet">
<style>
  :root {
    --yellow: #f5b91e;
    --gold: #b3843a;
    --charcoal: #404042;
    --text: #4a4a4c;
    --muted: #7a7a7c;
    --paper: #ffffff;
    --backdrop: #d6d7d9;
  }
  html, body {
    margin: 0;
    padding: 0;
    width: 1200px;
    height: 800px;
    overflow: hidden;
    background: var(--backdrop);
    font-family: "Montserrat", Arial, sans-serif;
  }
  .canvas {
    position: relative;
    width: 1200px;
    height: 800px;
  }
  .card {
    position: absolute;
    left: 346px;
    width: 510px;
    height: 283px;
    border-radius: 14px;
    overflow: hidden;
    background: var(--paper);
  }
  .card--front { top: 69px; }
  .card--back { top: 409px; }
  .card__shapes {
    position: absolute;
    inset: 0;
    width: 100%;
    height: 100%;
  }

  /* Front */
  .holder {
    position: absolute;
    left: 40px;
    top: 20px;
    text-align: center;
  }
  .holder__name {
    margin: 0;
    font-size: 24px;
    font-weight: 400;
    color: var(--yellow);
    line-height: 1.1;
  }
  .holder__title {
    margin: 0;
    font-size: 13px;
    color: var(--muted);
    line-height: 1.2;
  }
  .contact {
    position: absolute;
    left: 39px;
    margin: 0;
    padding: 0;
    list-style: none;
  }
  .contact__item {
    position: absolute;
    left: 0;
    display: flex;
    align-items: center;
    white-space: nowrap;
  }
  .contact__icon {
    width: 28px;
    height: 28px;
    border-radius: 50%;
    background: var(--yellow);
    flex: none;
  }
  .contact__icon svg { width: 28px; height: 28px; display: block; }
  .contact__text {
    margin-left: 14px;
    font-size: 14.5px;
    color: var(--text);
    line-height: 18px;
    letter-spacing: 0.2px;
  }
  .contact__item--phone { top: 85px; }
  .contact__item--address { top: 128px; }
  .contact__item--email { top: 169px; }
  .contact__item--web { top: 206px; }

  .brand {
    position: absolute;
    color: var(--gold);
    font-weight: 600;
    text-align: center;
    line-height: 1;
  }
  .brand__name { display: block; letter-spacing: 0.5px; }
  .brand__tag { display: block; letter-spacing: 0.4px; }
  .brand--front { left: 300px; top: 78px; width: 180px; }
  .brand--front .brand__name { font-size: 26px; }
  .brand--front .brand__tag { font-size: 8px; margin-top: 4px; }
  .brand--back { left: 75px; top: 128px; width: 260px; }
  .brand--back .brand__name { font-size: 38px; }
  .brand--back .brand__tag { font-size: 11.5px; margin-top: 6px; }
</style>
</head>
<body>
<main class="canvas">

  <section class="card card--front" aria-label="Business card front">
    <svg class="card__shapes" viewBox="0 0 637 354" preserveAspectRatio="none" aria-hidden="true">
      <rect x="0" y="318" width="440" height="36" fill="var(--charcoal)"/>
      <path d="M548 0 H637 V354 H400 C520 250 600 150 600 40 C600 20 580 5 548 0 Z" fill="var(--gold)"/>
      <path d="M637 148 V354 H422 C510 290 600 230 637 148 Z" fill="var(--charcoal)"/>
      <path d="M583 28 C600 120 540 230 438 354 L450 354 C555 235 612 125 583 28 Z" fill="var(--yellow)"/>
    </svg>

    <header class="holder">
      <h1 class="holder__name">Dax Falkrin</h1>
      <p class="holder__title">President and CEO</p>
    </header>

    <ul class="contact">
      <li class="contact__item contact__item--phone">
        <span class="contact__icon">
          <svg viewBox="0 0 28 28" aria-hidden="true"><rect x="10" y="7" width="8" height="14" rx="1.5" fill="none" stroke="#fff" stroke-width="1.5"/><circle cx="14" cy="18.5" r="0.9" fill="#fff"/></svg>
        </span>
        <span class="contact__text">403- 718-4063<br>403- 294-5170</span>
      </li>
      <li class="contact__item contact__item--address">
        <span class="contact__icon">
          <svg viewBox="0 0 28 28" aria-hidden="true"><path d="M14 22 C10 17 9 14.5 9 12.5 A5 5 0 0 1 19 12.5 C19 14.5 18 17 14 22 Z" fill="#fff"/><circle cx="14" cy="12.5" r="1.8" fill="var(--yellow)"/></svg>
        </span>
        <span class="contact__text">2871 96th Avenue<br>Velden, Alberta</span>
      </li>
      <li class="contact__item contact__item--email">
        <span class="contact__icon">
          <svg viewBox="0 0 28 28" aria-hidden="true"><rect x="7.5" y="9.5" width="13" height="9" fill="none" stroke="#fff" stroke-width="1.4"/><path d="M7.5 9.5 L14 15 L20.5 9.5" fill="none" stroke="#fff" stroke-width="1.4"/></svg>
        </span>
        <span class="contact__text">falkrinhomes@maildrop-example.net</span>
      </li>
      <li class="contact__item contact__item--web">
        <span class="contact__icon">
          <svg viewBox="0 0 28 28" aria-hidden="true"><circle cx="14" cy="14" r="7" fill="none" stroke="#fff" stroke-width="1.4"/><ellipse cx="14" cy="14" rx="3" ry="7" fill="none" stroke="#fff" stroke-width="1.2"/><line x1="7" y1="14" x2="21" y2="14" stroke="#fff" stroke-width="1.2"/></svg>
        </span>
        <span class="contact__text">www.falkrinhomes-example.com</span>
      </li>
    </ul>

    <div class="brand brand--front">
      <span class="brand__name">FALKRIN</span>
      <span class="brand__tag">HOMES AND RENOVATIONS</span>
    </div>
  </section>

  <section class="card card--back" aria-label="Business card back">
    <svg class="card__shapes" viewBox="0 0 637 354" preserveAspectRatio="none" aria-hidden="true">
      <path d="M520 0 H637 V354 H540 C560 270 580 210 560 205 C600 160 600 60 520 0 Z" fill="var(--gold)"/>
      <path d="M0 250 C40 310 150 320 260 318 C340 316 400 305 430 290 L330 354 H0 Z" fill="var(--yellow)"/>
      <path d="M637 146 V354 H318 Z" fill="var(--charcoal)"/>
    </svg>

    <div class="brand brand--back">
      <span class="brand__name">FALKRIN</span>
      <span class="brand__tag">HOMES AND RENOVATIONS</span>
    </div>
  </section>

</main>
</body>
</html>
```